Looking for business card/letterhead/email signature

Take existing logo and create full design suite of collateral

Contact Information for Business Card

Use mock details that can be edited by us

Font styles to use
Sans Serif

```html
<!DOCTYPE html>
<html lang="en">
<head>
<meta charset="utf-8">
<title>Marlow Digital Letterhead</title>
<link rel="stylesheet" href="https://fonts.googleapis.com/css2?family=Montserrat:wght@400;700&display=swap">
<style>
  :root {
    --backdrop: #9dbfdc;
    --paper: #ffffff;
    --navy: #1f3f8f;
    --ink: #4a4f57;
    --teal: #3fb3c8;
    --blue: #35a8e0;
    --lime: #cfd63a;
    --magenta: #e0287a;
    --orange: #f08a12;
    --charcoal: #4b4d50;
    --grey: #9a9ca0;
  }
  * { margin: 0; padding: 0; box-sizing: border-box; }
  html, body { width: 1200px; height: 784px; overflow: hidden; }
  body { background: var(--backdrop); font-family: "Montserrat", sans-serif; }

  .letterhead {
    position: absolute; left: 314px; top: 22px;
    width: 572px; height: 740px;
    background: linear-gradient(180deg, var(--paper) 70%, #eef2fb 100%);
    box-shadow: 0 8px 24px rgba(40, 70, 110, .25);
    overflow: hidden;
  }
  .header-swoosh { position: absolute; left: 0; top: 0; width: 572px; height: 220px; }

  .corner-strip { position: absolute; display: flex; height: 4px; width: 44px; }
  .corner-strip span { flex: 1; }
  .corner-strip--left { left: 0; top: 0; }
  .corner-strip--right { right: 0; top: 0; }

  .brand {
    position: absolute; left: 34px; top: 34px;
    display: flex; align-items: center; gap: 10px;
  }
  .brand__dot { width: 16px; height: 16px; border-radius: 50%; background: var(--navy); }
  .brand__name { font-weight: 700; font-size: 22px; color: var(--navy); letter-spacing: -.2px; }

  .contact {
    position: absolute; right: 26px; top: 130px;
    list-style: none; text-align: right;
    font-size: 7.5px; line-height: 11px; color: var(--ink);
  }
  .contact li { display: flex; justify-content: flex-end; align-items: flex-start; gap: 5px; }
  .contact__icon { width: 6px; height: 6px; margin-top: 2px; flex: none; }

  .footer-tabs { position: absolute; left: -6px; bottom: 0; width: 600px; height: 14px; }
</style>
</head>
<body>
  <main class="letterhead">
    <svg class="header-swoosh" viewBox="0 0 572 220" aria-hidden="true">
      <defs>
        <linearGradient id="swooshTint" x1="0" y1="0" x2="1" y2="0">
          <stop offset="0" stop-color="#e9ebf0"/>
          <stop offset=".45" stop-color="#f9e6ee"/>
          <stop offset=".75" stop-color="#f6f5dc"/>
          <stop offset="1" stop-color="#f8e7d6"/>
        </linearGradient>
      </defs>
      <path d="M0 0 H572 V210 C470 150 300 80 0 62 Z" fill="url(#swooshTint)"/>
      <path d="M0 70 C250 80 420 130 572 200" fill="none" stroke="#ffffff" stroke-width="6" opacity=".9"/>
      <path d="M60 92 C280 100 440 150 572 214" fill="none" stroke="#ffffff" stroke-width="3" opacity=".8"/>
    </svg>

    <div class="corner-strip corner-strip--left">
      <span style="background:var(--blue)"></span><span style="background:var(--lime)"></span><span style="background:var(--magenta)"></span><span style="background:var(--orange)"></span><span style="background:var(--charcoal)"></span>
    </div>
    <div class="corner-strip corner-strip--right">
      <span style="background:var(--charcoal)"></span><span style="background:var(--orange)"></span><span style="background:var(--magenta)"></span><span style="background:var(--lime)"></span><span style="background:var(--blue)"></span>
    </div>

    <div class="brand">
      <span class="brand__dot"></span>
      <span class="brand__name">Marlow Digital</span>
    </div>

    <ul class="contact">
      <li><span>12 Harbour Lane, Suite 4,<br>Exampleton EX4 2AB</span>
        <svg class="contact__icon" viewBox="0 0 10 10"><path d="M5 0a3.5 3.5 0 0 0-3.5 3.5C1.5 6 5 10 5 10s3.5-4 3.5-6.5A3.5 3.5 0 0 0 5 0z" fill="var(--teal)"/></svg></li>
      <li><span>000-000-0000</span>
        <svg class="contact__icon" viewBox="0 0 10 10"><path d="M2 0h2l1 3-1.5 1a6 6 0 0 0 2.5 2.5L7 5l3 1v2a2 2 0 0 1-2 2A8 8 0 0 1 0 2a2 2 0 0 1 2-2z" fill="var(--teal)"/></svg></li>
      <li><span>000-000-0000</span>
        <svg class="contact__icon" viewBox="0 0 10 10"><rect x="1" y="3" width="8" height="6" fill="var(--teal)"/><rect x="3" y="0" width="4" height="3" fill="var(--teal)"/></svg></li>
      <li><span>info@marlowdigital.com</span>
        <svg class="contact__icon" viewBox="0 0 10 10"><rect x="0" y="2" width="10" height="7" fill="var(--teal)"/><path d="M0 2l5 4 5-4" fill="none" stroke="#fff"/></svg></li>
      <li><span>www.marlowdigital.com</span>
        <svg class="contact__icon" viewBox="0 0 10 10"><circle cx="5" cy="5" r="5" fill="var(--teal)"/></svg></li>
    </ul>

    <svg class="footer-tabs" viewBox="0 0 600 14" aria-hidden="true">
      <defs>
        <linearGradient id="greyFade" x1="0" y1="0" x2="1" y2="0">
          <stop offset="0" stop-color="var(--grey)"/>
          <stop offset="1" stop-color="#e6e7ea"/>
        </linearGradient>
      </defs>
      <polygon points="0,0 70,0 64,14 0,14" fill="var(--blue)"/>
      <polygon points="86,0 176,0 170,14 80,14" fill="var(--lime)"/>
      <polygon points="192,0 266,0 260,14 186,14" fill="var(--magenta)"/>
      <polygon points="282,0 370,0 364,14 276,14" fill="var(--orange)"/>
      <polygon points="386,0 472,0 466,14 380,14" fill="var(--charcoal)"/>
      <polygon points="488,0 600,0 600,14 482,14" fill="url(#greyFade)"/>
    </svg>
  </main>
</body>
</html>
```